Irrigation Business needs their business cards modernised and revamped

I would like to keep my current logo, colours and revamp the format of the card.

I would like the card to be clean yet important.

Im not sure if you include texture but i would like the named logo to be indented into the card etc.

show me something alive and free something thats clinical to the point yet has a feel of achievement. i would like people to go nice card.

Target Market(s)

high end clients, corporate, sports field manger, the guys that make the decisions

Industry/Entity Type

Business

Contact Information for Business Card

nformation to be included

Dean Harlow (Director)
0487305526
dean@kolvat.biz
www.kestonfieldworks.com

instagram logo
google logo
facebook logo

Colors

Designer to choose colors to be used in the design.

Requirements
Nice to have
• indentations a really nice feel to the card good texture

```html
<!DOCTYPE html>
<html lang="en">
<head>
<meta charset="utf-8">
<title>Keston Fieldworks – Business Card</title>
<link rel="stylesheet" href="https://fonts.googleapis.com/css2?family=Montserrat:wght@800&family=Open+Sans:wght@400;700&display=swap">
<style>
  :root {
    --page: #e9ecef;
    --blue-deep: #2f64a8;
    --blue-mid: #3a86cf;
    --blue-light: #3aaedf;
    --blue-sky: #4cb9e6;
    --navy: #2b5a9e;
    --white: #ffffff;
  }
  * { box-sizing: border-box; margin: 0; padding: 0; }
  html, body {
    width: 1200px; height: 900px; overflow: hidden;
    background: var(--page);
  }
  .canvas {
    width: 1200px; height: 900px;
    display: flex; flex-direction: column; align-items: center; justify-content: center;
    gap: 40px;
  }
  .card {
    position: relative;
    width: 700px; height: 400px;
    overflow: hidden;
    box-shadow: 0 10px 28px rgba(0,0,0,0.18);
  }

  /* Front */
  .card-front {
    background: linear-gradient(110deg, var(--blue-sky) 0%, var(--blue-mid) 45%, var(--blue-deep) 100%);
    display: flex; flex-direction: column; align-items: center; justify-content: center;
    gap: 26px;
  }
  .brand {
    display: flex; align-items: center; gap: 18px;
  }
  .brand-dot {
    width: 64px; height: 64px; border-radius: 50%;
    border: 4px solid var(--white);
  }
  .brand-name {
    font-family: "Montserrat", sans-serif; font-weight: 800;
    font-size: 36px; letter-spacing: 0.5px; text-transform: uppercase;
    color: var(--white);
  }
  .social {
    display: flex; gap: 10px;
  }
  .social-dot {
    width: 22px; height: 22px; border-radius: 50%;
    background: var(--white);
  }

  /* Back */
  .card-back { background: var(--blue-light); }
  .card-back svg.back-shape { position: absolute; inset: 0; }
  .back-brand {
    position: absolute; left: 395px; top: 120px;
    display: flex; flex-direction: column; align-items: center; gap: 12px;
  }
  .back-brand .brand-dot { width: 56px; height: 56px; border-color: var(--navy); }
  .back-brand .brand-name { color: var(--navy); font-size: 28px; }

  .contact {
    position: absolute; left: 50px; top: 225px;
    font-family: "Open Sans", sans-serif; color: var(--white);
  }
  .contact-name { font-weight: 700; font-size: 18px; text-transform: uppercase; }
  .contact-role { font-size: 16px; text-transform: uppercase; margin-bottom: 14px; }
  .contact-list { list-style: none; }
  .contact-list li {
    display: flex; align-items: center; gap: 10px;
    font-size: 16px; line-height: 26px;
  }
  .contact-list svg { width: 16px; height: 16px; flex: none; }
</style>
</head>
<body>
<main class="canvas">

  <section class="card card-front">
    <div class="brand">
      <span class="brand-dot"></span>
      <span class="brand-name">Keston Fieldworks</span>
    </div>
    <div class="social">
      <span class="social-dot"></span>
      <span class="social-dot"></span>
      <span class="social-dot"></span>
    </div>
  </section>

  <section class="card card-back">
    <svg class="back-shape" width="700" height="400" viewBox="0 0 700 400">
      <circle cx="560" cy="150" r="272" fill="none" stroke="var(--navy)" stroke-width="14" stroke-dasharray="34 8"/>
      <circle cx="560" cy="150" r="258" fill="var(--white)"/>
    </svg>
    <div class="back-brand">
      <span class="brand-dot"></span>
      <span class="brand-name">Keston Fieldworks</span>
    </div>
    <div class="contact">
      <p class="contact-name">Dean Harlow</p>
      <p class="contact-role">Director</p>
      <ul class="contact-list">
        <li>
          <svg viewBox="0 0 16 16"><path fill="#fff" d="M3 1h3l1.5 4-2 1.2a9 9 0 0 0 4.3 4.3L11 8.5l4 1.5v3a2 2 0 0 1-2 2A12 12 0 0 1 1 3a2 2 0 0 1 2-2z"/></svg>
          0487305526
        </li>
        <li>
          <svg viewBox="0 0 16 16"><rect x="1" y="3" width="14" height="10" rx="1" fill="#fff"/><path d="M1.5 3.5 8 9l6.5-5.5" fill="none" stroke="var(--blue-light)" stroke-width="1.4"/></svg>
          dean@kolvat.biz
        </li>
        <li>
          <svg viewBox="0 0 16 16"><circle cx="8" cy="8" r="7" fill="none" stroke="#fff" stroke-width="1.5"/><ellipse cx="8" cy="8" rx="3" ry="7" fill="none" stroke="#fff" stroke-width="1.2"/><path d="M1 8h14" stroke="#fff" stroke-width="1.2"/></svg>
          www.kestonfieldworks.com
        </li>
      </ul>
    </div>
  </section>

</main>
</body>
</html>
```